A Modern & Sleek "Coming Soon" Page for an A.I Recruiting App

For the “Coming Soon” website, a simple background with no people in it. I've attached an A.I image of what the page should generally look like.

- A single mobile phone as the main focus where the user actually clicks on the, “notify me” button (after entering their email address).
- In the background where the pillars/columns are seen in the example, should be subtle pad locks that are in their opened position with a key inside the lock. I've attached images to try to illustrate this idea, but they are far away in style from what I'm looking for.

SLOGAN: Unlocking the power of meaningful connections
LOGO/TITLE: Should be the name as shown in image with only the name "KelvoLink" on it
COLORS: Purplish/blue hues. Should not be too feminine
NOTE: The user should only click once when signing up/entering their email.

Product: A recruiting platform that matches employers/employees with A.I. and prioritizing cultural fit/values system before skills. The industry we are tackling first is the caregiving industry (nannies, tutors, elderly). All users will be background screened and that info lives on the blockchain. All users will have the option to review and be reviewed/rated.

```html
<!DOCTYPE html>
<html lang="en">
<head>
<meta charset="utf-8">
<title>KelvoLink — Coming Soon</title>
<link href="https://fonts.googleapis.com/css2?family=Roboto:wght@300;400;500;700&display=swap" rel="stylesheet">
<style>
  :root {
    --ink-white: #ffffff;
    --deep-navy: #1c1640;
    --night-purple: #3a1f5c;
    --wine: #8a1c45;
    --magenta: #c2407a;
    --footer-rose: #bf4b79;
    --lock-pink: #e052a8;
    --lock-violet: #b23ad8;
    --phone-frame: #e9e9ec;
    --screen-dark: #1e1e1e;
    --screen-mid: #3a3a3a;
    --input-fill: #4b4b4b;
    --muted-text: #d6d6d6;
  }
  * { box-sizing: border-box; margin: 0; padding: 0; }
  html, body { width: 1200px; height: 804px; overflow: hidden; }
  body { font-family: "Roboto", Arial, sans-serif; color: var(--ink-white); background: var(--deep-navy); }

  .page { position: relative; width: 1200px; height: 804px; overflow: hidden; }

  .hero-backdrop {
    position: absolute; inset: 0 0 79px 0;
    background:
      radial-gradient(ellipse 420px 200px at 300px 60px, rgba(196,40,90,.75), transparent 70%),
      radial-gradient(ellipse 500px 220px at 820px 120px, rgba(210,90,160,.55), transparent 70%),
      radial-gradient(ellipse 600px 260px at 900px 520px, rgba(90,70,170,.55), transparent 70%),
      radial-gradient(ellipse 500px 300px at 200px 500px, rgba(60,40,120,.6), transparent 70%),
      linear-gradient(180deg, var(--wine) 0%, var(--night-purple) 45%, var(--deep-navy) 100%);
  }

  .brand-corner {
    position: absolute; left: 58px; top: 36px;
    font-weight: 300; font-size: 36px; letter-spacing: 3px;
    text-transform: uppercase;
  }

  .lock-illustration {
    position: absolute; left: 17px; top: 210px; width: 257px; height: 428px;
    border-radius: 120px 120px 110px 110px;
    background: radial-gradient(ellipse at 40% 65%, var(--lock-pink), var(--lock-violet) 80%, transparent 100%);
    opacity: .9;
  }

  .phone {
    position: absolute; left: 272px; top: 103px; width: 221px; height: 596px;
    border-radius: 38px; background: var(--phone-frame);
    padding: 7px;
    box-shadow: 0 20px 40px rgba(0,0,0,.45);
  }
  .phone-screen {
    position: relative; width: 100%; height: 100%;
    border-radius: 32px;
    background: linear-gradient(180deg, var(--screen-mid) 0%, var(--screen-dark) 45%, #111 100%);
    overflow: hidden;
  }
  .phone-notch {
    position: absolute; left: 50%; top: 0; transform: translateX(-50%);
    width: 104px; height: 20px; background: #0c0c0c; border-radius: 0 0 14px 14px;
  }
  .app-title {
    position: absolute; top: 178px; width: 100%; text-align: center;
    font-weight: 700; font-size: 22px; letter-spacing: .5px; text-transform: uppercase;
  }
  .email-prompt {
    position: absolute; top: 272px; width: 100%; text-align: center;
    font-weight: 400; font-size: 18px; color: var(--muted-text);
  }
  .email-field {
    position: absolute; left: 30px; top: 317px; width: 147px; height: 32px;
    border: none; border-radius: 4px; background: var(--input-fill);
    color: var(--muted-text); font: 400 11px "Roboto", Arial, sans-serif; padding: 0 9px;
  }
  .email-field::placeholder { color: var(--muted-text); }
  .notify-button {
    position: absolute; left: 54px; top: 385px; width: 120px; height: 46px;
    border: 2px solid var(--ink-white); border-radius: 23px;
    background: #000; color: var(--ink-white);
    font: 700 14px "Roboto", Arial, sans-serif; letter-spacing: .3px;
    box-shadow: 0 0 12px rgba(255,255,255,.35);
  }
  .home-bar {
    position: absolute; left: 50%; bottom: 10px; transform: translateX(-50%);
    width: 58px; height: 3px; border-radius: 2px; background: #ddd;
  }

  .brand-headline {
    position: absolute; left: 600px; top: 280px;
    font-weight: 300; font-size: 78px; letter-spacing: 4px; text-transform: uppercase;
    line-height: 1;
  }
  .slogan {
    position: absolute; left: 600px; top: 388px;
    font-weight: 400; font-size: 24px;
  }

  .site-footer {
    position: absolute; left: 0; bottom: 0; width: 100%; height: 79px;
    background: var(--footer-rose);
    display: flex; align-items: center; justify-content: center;
    font-weight: 700; font-size: 15.5px; letter-spacing: .3px; text-transform: uppercase;
  }
  .site-footer .divider { margin: 0 14px; }
</style>
</head>
<body>
  <main class="page">
    <div class="hero-backdrop" role="img" aria-label="Abstract glowing purple and magenta waves with soft light particles"></div>

    <div class="brand-corner">KelvoLink</div>

    <div class="lock-illustration" role="img" aria-label="Pink 3D open padlock with a key inserted"></div>

    <div class="phone">
      <div class="phone-screen">
        <div class="phone-notch"></div>
        <div class="app-title">KelvoLink</div>
        <div class="email-prompt">Enter Email Here</div>
        <input class="email-field" type="email" placeholder="Enter Email">
        <button class="notify-button" type="button">NOTIFY ME</button>
        <div class="home-bar"></div>
      </div>
    </div>

    <h1 class="brand-headline">KelvoLink</h1>
    <p class="slogan">Unlocking the power of meaningful connections</p>

    <footer class="site-footer">
      <span>©Copyrights 2024 KelvoLink</span><span class="divider">|</span><span>All Rights Reserved</span>
    </footer>
  </main>
</body>
</html>
```